Health Wellbeing Beauty online Shop

I have attached a full spec, however in summary this is a new business startup selling skincare products.

We need a web design for new wellbeing website, selling skincare products so need an eCommerce solution . On the home page I would like these faces to dissolve into each other on a loop or use a honeycomb style transation.
You will need the option of being able to log into an account, either through lumigram, vexora, chirplo or create an account. For created accounts, obviously need the facility to be able to reset passwords, see previous orders, track current order, and maintain favourites.
It should be PC, mobile and tablet friendly.

Look and Feel
It should be an elegant, modern, professional, trendy, unisex website. It should look clean and calm. Am happy to try interesting and slightly unusual designs. I would also like to have chat functionality, either powered by talvuNchat or by Quo 58.
Websites I like are
https://www.nobel-radiance.example.co.uk/
https://www.mereminerals.example.co.uk/
http://www.brightdermis.example.com/

PLEASE DO USE YOUR KNOWELDGE OF WHAT WORKS FOR WEB DESIGN. YOU’RE THE EXPERT AND NEED YOUR EXPERTISE. CARTE BLANCHE TO DESIGN AS YOU SEE FIT. Please be creative, I need my site to stand out from the crowd.

Target Market(s)

Target Market
Middle aged women are our most common client, however, younger patients, both male and female, will often visit the site. In summary, I would like the site to appeal to all age brackets.

Industry/Entity Type

Business

Coding

Coded - Design and coding required

Number of Pages Required

4 page

Requirements
Must have
• Need shop to be exactly like shop on this link http://www.brightdermis.example.com/
Nice to have
• i would like something unique and creative

```html
<!DOCTYPE html>
<html lang="en">
<head>
<meta charset="utf-8">
<title>Lumora Skin Clinic</title>
<link rel="stylesheet" href="https://fonts.googleapis.com/css2?family=Montserrat:wght@300;400;500;600&family=Open+Sans:ital,wght@0,400;0,600;1,400&display=swap">
<style>
:root{
  --gold:#c9a24c;
  --gold-mid:#e3c566;
  --yellow:#f3c934;
  --footer:#d3b764;
  --ink:#222;
  --line:#e2e2e2;
  --hero:#ececec;
  --white:#fff;
  --price:#d49b27;
  --icon:#d5a63c;
}
*{box-sizing:border-box;margin:0;padding:0}
html,body{width:1200px;height:2384px;overflow:hidden}
body{position:relative;background:var(--white);font-family:"Montserrat",Arial,sans-serif;color:var(--ink)}

/* header */
.site-header{position:absolute;left:0;top:0;width:1200px;height:132px;background:var(--white)}
.brand{position:absolute;left:130px;top:0;width:200px;height:132px;display:flex;align-items:center;justify-content:center;gap:12px}
.brand-dot{width:18px;height:18px;border-radius:50%;background:var(--gold)}
.brand-name{font-size:36px;font-weight:400;color:#444;letter-spacing:2px}
.search{position:absolute;left:410px;top:56px;width:357px;height:42px;border:1.5px solid #bdbdbd;display:flex;align-items:center;padding-left:14px;gap:10px;font-size:14px;color:#888}
.header-tools{position:absolute;left:802px;top:0;height:132px;display:flex;border-left:1px solid var(--line)}
.tool{width:92px;height:132px;border-right:1px solid var(--line);text-align:center;padding-top:32px;font-size:13px;line-height:17px;color:#333;position:relative}
.tool:last-child{width:104px}
.tool svg{display:block;margin:0 auto 8px}
.cart-count{position:absolute;left:58px;top:18px;width:20px;height:20px;border-radius:50%;background:var(--gold);color:#fff;font-size:11px;line-height:20px}

/* nav */
.main-nav{position:absolute;left:0;top:132px;width:1200px;height:56px;background:linear-gradient(#d7b25a,#c49a40 60%,#b98f38);display:flex;justify-content:center}
.main-nav a{color:#fff;text-decoration:none;font-size:15.5px;line-height:56px;padding:0 13px;border-right:1px solid rgba(255,255,255,.35)}
.main-nav a:last-child{border-right:0}

/* hero */
.hero{position:absolute;left:0;top:188px;width:1200px;height:436px;background:radial-gradient(circle at 70% 50%,#f6f6f6,var(--hero) 70%)}
.hero-title{position:absolute;left:118px;top:120px;font-size:41px;font-weight:400;color:#111}
.hero-sub{position:absolute;left:117px;top:172px;font-size:44px;font-weight:300;color:#555;letter-spacing:1px}
.hero-text{position:absolute;left:119px;top:232px;width:440px;font-size:14px;line-height:20px;color:#555}
.hero-dots{position:absolute;left:122px;top:289px;display:flex;gap:5px}
.hero-dots span{width:15px;height:15px;border-radius:50%;background:#888}
.hero-dots span:first-child{background:transparent;border:2px solid #888}
.hero-faces{position:absolute;left:0;top:0}

/* welcome */
.welcome{position:absolute;left:0;top:624px;width:1200px;height:286px;background:linear-gradient(160deg,#fff 40%,#f3f3f3 70%,#fff)}
.welcome h1{position:absolute;top:44px;width:1200px;text-align:center;font-size:34px;font-weight:400}
.welcome h1 span{color:var(--gold)}
.welcome p{position:absolute;left:180px;top:103px;width:858px;text-align:center;font-family:"Open Sans",Arial,sans-serif;font-size:14px;line-height:24px;color:#666}
.btn-read{position:absolute;left:527px;top:198px;width:137px;height:44px;background:var(--gold);color:#fff;font-size:13px;letter-spacing:1px;text-align:center;line-height:44px;outline:1.5px solid var(--gold);outline-offset:3px}

.features{position:absolute;left:122px;top:931px;display:flex;gap:11px}
.feature{width:311px;height:269px;position:relative;color:#fff;text-align:center}
.feature::after{content:"";position:absolute;inset:7px;border:1.5px solid rgba(255,255,255,.7)}
.feature.one{background:var(--gold)}
.feature.two{background:var(--gold-mid)}
.feature.three{background:var(--yellow)}
.feature svg{margin-top:35px}
.feature h3{font-size:20px;font-weight:500;margin-top:12px}
.feature p{font-family:"Open Sans",Arial,sans-serif;font-size:12px;line-height:20px;margin:12px auto 0;width:240px;opacity:.9}

/* products */
.featured-title{position:absolute;left:130px;top:1270px;font-size:25px;font-weight:400;letter-spacing:.5px;color:#333}
.select{position:absolute;top:1273px;height:32px;border:1px solid #ccc;font-size:11px;color:#777;padding:0 10px;line-height:30px;background:#fff}
.select::after{content:"";position:absolute;right:10px;top:9px;width:7px;height:7px;border-right:1.5px solid #666;border-bottom:1.5px solid #666;transform:rotate(45deg)}
.arrow-btn{position:absolute;top:1273px;width:33px;height:32px;background:#e4e4e4;display:flex;align-items:center;justify-content:center}
.products{position:absolute;left:111px;top:1330px;display:flex}
.product{width:241px;height:330px;border-right:1px solid #ddd;position:relative}
.product:last-child{border-right:0}
.product-photo{position:absolute;left:40px;top:20px;width:160px;height:150px;border-radius:4px}
.product h4{position:absolute;left:32px;top:201px;font-size:17px;font-weight:500;color:#111}
.product .desc{position:absolute;left:32px;top:228px;font-family:"Open Sans",Arial,sans-serif;font-size:11px;color:#555}
.product .price{position:absolute;left:32px;top:250px;font-size:19px;color:var(--price)}
.product .stars{position:absolute;left:152px;top:251px;font-size:16px;color:#f0b323;letter-spacing:1px}
.product .buy{position:absolute;left:32px;top:284px;width:95px;height:27px;border:1.5px solid var(--gold);font-size:11px;color:var(--gold);text-align:center;line-height:25px}

/* testimonial */
.testimonial{position:absolute;left:0;top:1724px;width:1200px;height:304px;background:linear-gradient(100deg,#3c2a28,#6d5049 45%,#7a5e55 60%,#433330)}
.testimonial h2{position:absolute;top:60px;width:1200px;text-align:center;color:#fff;font-size:24px;font-weight:400}
.testimonial blockquote{position:absolute;left:290px;top:110px;width:620px;text-align:center;font-family:"Open Sans",Arial,sans-serif;font-style:italic;color:#fff;font-size:16px;line-height:30px}
.quote-mark{position:absolute;top:100px;color:#fff;font-family:Georgia,serif;font-size:70px;line-height:70px;font-weight:700}
.t-arrow{position:absolute;top:132px}
.author{position:absolute;left:508px;top:172px;display:flex;align-items:center;gap:10px}
.avatar{width:56px;height:56px;border-radius:50%;background:radial-gradient(#e2c2a8,#a87b62);border:3px solid #fff}
.author b{display:block;font-family:"Open Sans",Arial,sans-serif;font-weight:400;color:#fff;font-size:16px}
.author span{font-family:"Open Sans",Arial,sans-serif;color:#c8b2a6;font-size:15px}

/* footer */
.site-footer{position:absolute;left:0;top:2028px;width:1200px;height:356px;background:var(--footer);color:#fff}
.f-col{position:absolute;top:46px}
.f-col h5{font-size:15px;font-weight:500;letter-spacing:.5px;margin-bottom:16px}
.f-col li{list-style:none;font-family:"Open Sans",Arial,sans-serif;font-size:13px;line-height:30px;padding-left:3px}
.contact p{font-family:"Open Sans",Arial,sans-serif;font-size:13px;line-height:19px;margin-bottom:16px}
.newsletter p{font-family:"Open Sans",Arial,sans-serif;font-size:13px;margin-bottom:10px}
.signup{display:flex;height:36px;margin-left:3px}
.signup .field{width:183px;background:#fff;color:#999;font-size:11px;line-height:36px;padding-left:14px}
.signup .go{width:101px;background:#2a2a2a;color:#fff;font-size:13px;font-weight:600;line-height:36px;text-align:center}
.pay{display:flex;gap:8px;margin:17px 0 0 3px}
.pay span{width:42px;height:22px;background:#fff;border-radius:2px;font-family:"Open Sans",Arial,sans-serif;font-size:9px;font-weight:600;color:#555;text-align:center;line-height:22px}
.social{display:flex;gap:10px;margin:18px 0 0 3px;width:380px}
.social span{display:flex;align-items:center;gap:4px;font-family:"Open Sans",Arial,sans-serif;font-size:11px}
.social i{width:30px;height:30px;border-radius:50%;background:#8f7a44;display:block}
.f-rule{position:absolute;left:111px;top:303px;width:982px;height:1px;background:rgba(255,255,255,.6)}
.copyright{position:absolute;top:322px;width:1200px;text-align:center;font-family:"Open Sans",Arial,sans-serif;font-size:12px}
</style>
</head>
<body>

<header class="site-header">
  <div class="brand"><span class="brand-dot"></span><span class="brand-name">Lumora</span></div>
  <div class="search">
    <svg width="18" height="18" viewBox="0 0 18 18"><circle cx="7.5" cy="7.5" r="5.5" fill="none" stroke="#999" stroke-width="2"/><line x1="11.5" y1="11.5" x2="16" y2="16" stroke="#999" stroke-width="2"/></svg>
    Search Product here
  </div>
  <div class="header-tools">
    <div class="tool">
      <span class="cart-count">8</span>
      <svg width="36" height="40" viewBox="0 0 36 40"><path d="M4 12h28l-2 26H6z" fill="none" stroke="#d5a63c" stroke-width="2.5"/><path d="M12 14V8a6 6 0 0 1 12 0v6" fill="none" stroke="#d5a63c" stroke-width="2.5"/></svg>
      My Cart
    </div>
    <div class="tool">
      <svg width="36" height="40" viewBox="0 0 36 40"><circle cx="18" cy="12" r="9" fill="#d5a63c"/><path d="M2 40c0-12 7-17 16-17s16 5 16 17z" fill="#d5a63c"/></svg>
      Create an<br>Account
    </div>
    <div class="tool">
      <svg width="36" height="40" viewBox="0 0 36 40"><circle cx="18" cy="22" r="12" fill="#d5a63c"/></svg>
      Login with<br>lumigram
    </div>
  </div>
</header>

<nav class="main-nav">
  <a>Skin Lightening Tablets</a><a>Skin Lightening Creams</a><a>Skin Lightening Soaps</a><a>Skin Lightening Vials</a><a>Contact</a><a>About Us</a>
</nav>

<section class="hero">
  <h2 class="hero-title">Lumora Skin Clinic</h2>
  <div class="hero-sub">Skin Specialist &amp; Care</div>
  <p class="hero-text">Mauris vel lacus vitae felis vestibulum volutpat Etiam est nunc venenatis in tristique eu imperdiet ac nisl</p>
  <div class="hero-dots"><span></span><span></span><span></span><span></span></div>
  <svg class="hero-faces" width="1200" height="436" viewBox="0 0 1200 436" role="img" aria-label="Honeycomb of seven customer portrait photos">
    <defs>
      <linearGradient id="skin1" x1="0" y1="0" x2="1" y2="1"><stop offset="0" stop-color="#e9cdb6"/><stop offset="1" stop-color="#b88e72"/></linearGradient>
      <linearGradient id="skin2" x1="0" y1="0" x2="1" y2="1"><stop offset="0" stop-color="#9a6a4e"/><stop offset="1" stop-color="#3b2a22"/></linearGradient>
      <linearGradient id="skin3" x1="0" y1="0" x2="1" y2="1"><stop offset="0" stop-color="#f0dccb"/><stop offset="1" stop-color="#c9a78f"/></linearGradient>
      <polygon id="hex" points="-70,0 -36,-64 36,-64 70,0 36,64 -36,64"/>
    </defs>
    <g stroke="#fff" stroke-width="5">
      <use href="#hex" x="815" y="71" fill="url(#skin2)"/>
      <use href="#hex" x="678" y="138" fill="url(#skin3)"/>
      <use href="#hex" x="936" y="138" fill="url(#skin2)"/>
      <use href="#hex" x="815" y="206" fill="url(#skin1)"/>
      <use href="#hex" x="678" y="284" fill="url(#skin1)"/>
      <use href="#hex" x="936" y="284" fill="url(#skin1)"/>
      <use href="#hex" x="815" y="349" fill="url(#skin3)"/>
    </g>
  </svg>
</section>

<section class="welcome">
  <h1>Welcome to <span>Lumora Skin Clinic</span></h1>
  <p>Curabitur iaculis tempus eros Curabitur vel mi sit amet magna malesuada ultrices Ut nisi erat fermentum vel congue id euismod in elit Fusce ultricies orci ac feugiat suscipit leo massa sodales velit et scelerisque mi tortor at ipsum cligula augue bibendum accumsan vestibulum ut commodo a mi Morbi ornare gravida elit Integer congue augue et malesuada iac</p>
  <div class="btn-read">READ MORE</div>
</section>

<div class="features">
  <div class="feature one">
    <svg width="120" height="106" viewBox="0 0 120 106"><polygon points="30,2 90,2 118,53 90,104 30,104 2,53" fill="none" stroke="#fff" stroke-width="2"/><circle cx="64" cy="44" r="15" fill="none" stroke="#fff" stroke-width="3"/><line x1="54" y1="56" x2="44" y2="72" stroke="#fff" stroke-width="5" stroke-linecap="round"/></svg>
    <h3>Skin Specialist</h3>
    <p>Mauris vel lacus vitae felis vestibulum volutpat Etiam est nunc venenat</p>
  </div>
  <div class="feature two">
    <svg width="120" height="106" viewBox="0 0 120 106"><polygon points="30,2 90,2 118,53 90,104 30,104 2,53" fill="none" stroke="#fff" stroke-width="2"/><circle cx="60" cy="53" r="18" fill="#fff"/><text x="60" y="61" text-anchor="middle" font-family="Montserrat,sans-serif" font-weight="700" font-size="22" fill="#e3c566">?</text></svg>
    <h3>Why Choose Us</h3>
    <p>Mauris vel lacus vitae felis vestibulum volutpat Etiam est nunc venenat</p>
  </div>
  <div class="feature three">
    <svg width="120" height="106" viewBox="0 0 120 106"><polygon points="30,2 90,2 118,53 90,104 30,104 2,53" fill="none" stroke="#fff" stroke-width="2"/><circle cx="60" cy="53" r="17" fill="none" stroke="#fff" stroke-width="3"/><ellipse cx="60" cy="53" rx="7" ry="17" fill="none" stroke="#fff" stroke-width="2"/><line x1="43" y1="53" x2="77" y2="53" stroke="#fff" stroke-width="2"/></svg>
    <h3>Global Shipping</h3>
    <p>Mauris vel lacus vitae felis vestibulum volutpat Etiam est nunc venenat</p>
  </div>
</div>

<h2 class="featured-title">FEATURED PRODUCTS</h2>
<div class="select" style="left:699px;width:135px">Sort by</div>
<div class="select" style="left:847px;width:133px">Categories</div>
<div class="arrow-btn" style="left:993px"><svg width="10" height="14"><path d="M8 1 2 7l6 6" fill="none" stroke="#333" stroke-width="2"/></svg></div>
<div class="arrow-btn" style="left:1036px"><svg width="10" height="14"><path d="M2 1l6 6-6 6" fill="none" stroke="#333" stroke-width="2"/></svg></div>

<div class="products">
  <div class="product">
    <div class="product-photo" role="img" aria-label="Makeup bottles and compact" style="background:linear-gradient(160deg,#f3e6dc,#c89a7c)"></div>
    <h4>Product Name</h4><div class="desc">Mauris vel lacus vitae felis vestibulum</div>
    <div class="price">$24.50</div><div class="stars">★★★★</div><div class="buy">BUY NOW</div>
  </div>
  <div class="product">
    <div class="product-photo" role="img" aria-label="White cream jar" style="background:linear-gradient(160deg,#f7f7f7,#d2d2d2)"></div>
    <h4>Product Name</h4><div class="desc">Mauris vel lacus vitae felis vestibulum</div>
    <div class="price">$24.50</div><div class="stars">★★★★</div><div class="buy">BUY NOW</div>
  </div>
  <div class="product">
    <div class="product-photo" role="img" aria-label="Cream jar with black lid" style="background:linear-gradient(110deg,#efefef 45%,#3a3a3a)"></div>
    <h4>Product Name</h4><div class="desc">Mauris vel lacus vitae felis vestibulum</div>
    <div class="price">$24.50</div><div class="stars">★★★★</div><div class="buy">BUY NOW</div>
  </div>
  <div class="product">
    <div class="product-photo" role="img" aria-label="Amber oil bottles and soap" style="background:linear-gradient(160deg,#f6e4b8,#d99a2b)"></div>
    <h4>Product Name</h4><div class="desc">Mauris vel lacus vitae felis vestibulum</div>
    <div class="price">$24.50</div><div class="stars">★★★★</div><div class="buy">BUY NOW</div>
  </div>
</div>

<section class="testimonial" role="img" aria-label="Dimmed photo of a woman applying face cream">
  <h2>What Our Customer Says</h2>
  <span class="quote-mark" style="left:244px">“</span>
  <span class="quote-mark" style="left:920px">”</span>
  <svg class="t-arrow" style="left:168px" width="20" height="36"><path d="M17 2 3 18l14 16" fill="none" stroke="#ccc" stroke-width="3"/></svg>
  <svg class="t-arrow" style="left:1018px" width="20" height="36"><path d="M3 2l14 16L3 34" fill="none" stroke="#ccc" stroke-width="3"/></svg>
  <blockquote>Mauris vel lacus vitae felis vestibulum volutpat Etiam est nunc venenatis in tristique eu imperdiet ac nisl Cum sociis natoque penatibus et magnis</blockquote>
  <div class="author">
    <div class="avatar" role="img" aria-label="Customer portrait"></div>
    <div><b>- By Author Name</b><span>City Location</span></div>
  </div>
</section>

<footer class="site-footer">
  <div class="f-col" style="left:119px">
    <h5>CATEGORIES</h5>
    <ul><li>Hair Growth</li><li>Beauty Face</li><li>Skin Creame</li><li>Latest Arrivals</li><li>Top Products</li></ul>
  </div>
  <div class="f-col" style="left:313px">
    <h5>COMPANY</h5>
    <ul><li>About Us</li><li>Privacy Policy</li><li>Shipping &amp; Returns</li><li>Testimonials</li><li>My Account</li></ul>
  </div>
  <div class="f-col contact" style="left:513px">
    <h5>CONTACT US</h5>
    <p>Calling from the UK<br>0800 555 0142</p>
    <p>Calling from Overseas<br>+44 800 555 0142</p>
    <p>Monday - Friday:<br>8am until 18:00pm</p>
  </div>
  <div class="f-col newsletter" style="left:771px">
    <h5>SIGN UP FOR NEWSLETTERS</h5>
    <p>Please sign up here for latest news</p>
    <div class="signup"><div class="field">EMAIL ADDRESS</div><div class="go">SUBSCRIBE</div></div>
    <div class="pay"><span>Payvo</span><span>Amerix</span><span>Findra</span><span>Cardmo</span><span>Paylo</span></div>
    <div class="social"><span><i></i>chirplo</span><span><i></i>lumigram</span><span><i></i>linkora</span><span><i></i>vexora</span></div>
  </div>
  <div class="f-rule"></div>
  <div class="copyright">© 2016 Company Name &nbsp;All right reserved &nbsp;Term of Use</div>
</footer>

</body>
</html>
```